Service Menu refresh 2018 Update of menu pricing

We currently have service menus as attached. We will be updating our look via our homepage image, our service menu and our in-house beverage and treatment menu.
We are a natural and sustainable hair salon group and moving more towards head spa which consists of treatments, beauty, tanning as well as your traditional hair services. Our imagery needs to reflect our efforts in spa treatments in the hair and scalp area and use natural materials and colours reflecting sustainability.
Velune is the brand we stock and promote.

Target Market(s)

Men or women interesting in personal maintenance with natural and organic products and using sustainable practises

Industry/Entity Type

Hair And Beauty

Font styles to use
Sans Serif
Other font styles liked:
• Arial or Helvetica

Colors
9acb3c
abd037
cadf82
ffffff

Requirements
Must have
• Name on the front cover, locations on back cover
Nice to have
• Prestige feel, reflect male and female clients
Should not have
• Bold artificial writing or any type of cartoon images.
• Same images as existing menu.

```html
<!DOCTYPE html>
<html lang="en">
<head>
<meta charset="utf-8">
<title>Verdant Roots Hair Salons — Service Menu</title>
<link href="https://fonts.googleapis.com/css2?family=Arimo:ital,wght@0,400;0,700;1,700&display=swap" rel="stylesheet">
<style>
:root{
  --leaf:#9acb3c;
  --lime:#abd037;
  --pale:#cadf82;
  --white:#ffffff;
  --ink:#222222;
  --grey:#8c8c8c;
  --grey-light:#ececec;
  --backdrop:#e3e4e6;
  --disc:#1f1d1e;
}
*{box-sizing:border-box;margin:0;padding:0}
html,body{width:807px;height:1200px;overflow:hidden}
body{background:var(--backdrop);font-family:"Arimo",Arial,Helvetica,sans-serif;color:var(--ink);position:relative}

.page{position:absolute;width:370px;height:370px;background:var(--white);box-shadow:0 2px 10px rgba(0,0,0,.12);overflow:hidden}

/* back cover */
.back-cover{left:24px;top:110px;padding:26px 26px 20px}
.back-cover .quote{font-weight:700;font-style:italic;font-size:15px;line-height:1.25;margin-bottom:12px}
.location{margin-bottom:7px}
.location h3{color:var(--leaf);font-size:9.5px;font-weight:700;text-transform:uppercase;letter-spacing:.2px;margin-bottom:1px}
.location p{display:flex;align-items:center;gap:5px;font-size:8.5px;line-height:1.35}
.location svg{width:8px;height:8px;flex:none;fill:var(--leaf)}
.back-cover .web{color:var(--leaf);font-weight:700;font-size:13.5px;letter-spacing:.4px;margin-top:6px}

/* front cover */
.front-cover{left:413px;top:110px}
.cover-photo{position:absolute;inset:0;background:
  radial-gradient(circle at 75% 25%,#7dbb3a 0,transparent 40%),
  radial-gradient(circle at 20% 80%,#c9a27a 0,transparent 22%),
  linear-gradient(160deg,#f4f9ea 0%,#c6e29a 45%,#8fc650 75%,#d9e9c4 100%)}
.brand-disc{position:absolute;left:70px;top:62px;width:150px;height:150px;border-radius:50%;background:var(--disc);display:flex;flex-direction:column;align-items:center;justify-content:center;text-align:center}
.brand-name{color:var(--white);font-size:15px;font-weight:400;line-height:1.25;letter-spacing:.3px}

/* inner spread */
.spread{position:absolute;left:24px;top:560px;width:759px;height:370px;display:flex;box-shadow:0 2px 10px rgba(0,0,0,.12)}
.spread .inner{position:relative;width:379.5px;height:370px;background:var(--white);padding:20px 20px 12px;display:flex;flex-direction:column}
.spread .inner.left{border-right:1px solid #d8d8d8}
.size-head{display:grid;grid-template-columns:1fr repeat(4,44px);height:18px;flex:none}
.size-head span{background:var(--grey);color:var(--white);font-size:9px;font-weight:700;display:flex;align-items:center;justify-content:center;border-left:1px solid var(--white)}
.size-head span.blank{background:var(--grey-light);border:none}
.section-band{background:var(--lime);color:var(--ink);font-size:10px;font-weight:700;text-transform:uppercase;padding:3px 6px;margin-top:6px}
.price-row{display:grid;grid-template-columns:1fr repeat(4,44px);font-size:8px;line-height:10px;border-bottom:1px solid var(--grey-light)}
.price-row .item{padding:2px 6px;text-transform:uppercase;font-weight:700}
.price-row .item.sub{text-transform:none;font-weight:400}
.price-row span:not(.item){padding:2px 0;text-align:center;background:#f6f6f6;border-left:1px solid var(--white)}
.note{font-size:7px;line-height:1.3;padding:4px 6px 0;color:#444}
.spread-foot{margin-top:auto;padding-top:6px;font-size:7.5px;color:#444;line-height:1.4}
</style>
</head>
<body>

<section class="page back-cover" aria-label="Back cover">
  <p class="quote">“Living a more natural and organic life is a philosophy not just a product certification”</p>

  <div class="location">
    <h3>Willowbank</h3>
    <p><svg viewBox="0 0 10 10"><path d="M5 0a3.5 3.5 0 0 0-3.5 3.5C1.5 6 5 10 5 10s3.5-4 3.5-6.5A3.5 3.5 0 0 0 5 0zm0 5a1.5 1.5 0 1 1 0-3 1.5 1.5 0 0 1 0 3z"/></svg>Shop 1018 Meadowgate Willowbank, Brook Rd, Willowbank</p>
    <p><svg viewBox="0 0 10 10"><path d="M2 0l2 2.5-1.2 1.3a6 6 0 0 0 3.4 3.4L7.5 6 10 8l-1.5 2C4 10 0 6 0 1.5z"/></svg>+61 (07) 5550 1101</p>
    <p><svg viewBox="0 0 10 10"><path d="M0 2h10v6H0zM0 2l5 3.5L10 2" stroke="#fff" stroke-width=".8"/></svg>willowbank@verdantroots.example</p>
  </div>

  <div class="location">
    <h3>Fernhill</h3>
    <p><svg viewBox="0 0 10 10"><path d="M5 0a3.5 3.5 0 0 0-3.5 3.5C1.5 6 5 10 5 10s3.5-4 3.5-6.5A3.5 3.5 0 0 0 5 0zm0 5a1.5 1.5 0 1 1 0-3 1.5 1.5 0 0 1 0 3z"/></svg>Shop 231 Meadowgate Fernhill, Cedar Road, Fernhill</p>
    <p><svg viewBox="0 0 10 10"><path d="M2 0l2 2.5-1.2 1.3a6 6 0 0 0 3.4 3.4L7.5 6 10 8l-1.5 2C4 10 0 6 0 1.5z"/></svg>+61 (07) 5550 1102</p>
    <p><svg viewBox="0 0 10 10"><path d="M0 2h10v6H0zM0 2l5 3.5L10 2" stroke="#fff" stroke-width=".8"/></svg>fernhill@verdantroots.example</p>
  </div>

  <div class="location">
    <h3>In Larkspur</h3>
    <p><svg viewBox="0 0 10 10"><path d="M5 0a3.5 3.5 0 0 0-3.5 3.5C1.5 6 5 10 5 10s3.5-4 3.5-6.5A3.5 3.5 0 0 0 5 0zm0 5a1.5 1.5 0 1 1 0-3 1.5 1.5 0 0 1 0 3z"/></svg>Shop 3082 Larkspur Shopping Centre, Hollow Rd</p>
    <p><svg viewBox="0 0 10 10"><path d="M2 0l2 2.5-1.2 1.3a6 6 0 0 0 3.4 3.4L7.5 6 10 8l-1.5 2C4 10 0 6 0 1.5z"/></svg>+61 (07) 5550 1103</p>
    <p><svg viewBox="0 0 10 10"><path d="M0 2h10v6H0zM0 2l5 3.5L10 2" stroke="#fff" stroke-width=".8"/></svg>larkspur@verdantroots.example</p>
  </div>

  <div class="location">
    <h3>Reedmere</h3>
    <p><svg viewBox="0 0 10 10"><path d="M5 0a3.5 3.5 0 0 0-3.5 3.5C1.5 6 5 10 5 10s3.5-4 3.5-6.5A3.5 3.5 0 0 0 5 0zm0 5a1.5 1.5 0 1 1 0-3 1.5 1.5 0 0 1 0 3z"/></svg>Shop 1255 Meadowgate Reedmere, Summit St, Reedmere</p>
    <p><svg viewBox="0 0 10 10"><path d="M2 0l2 2.5-1.2 1.3a6 6 0 0 0 3.4 3.4L7.5 6 10 8l-1.5 2C4 10 0 6 0 1.5z"/></svg>+61 (07) 5550 1104</p>
    <p><svg viewBox="0 0 10 10"><path d="M0 2h10v6H0zM0 2l5 3.5L10 2" stroke="#fff" stroke-width=".8"/></svg>reedmere@verdantroots.example</p>
  </div>

  <div class="location">
    <h3>Riverside General Hospital</h3>
    <p><svg viewBox="0 0 10 10"><path d="M5 0a3.5 3.5 0 0 0-3.5 3.5C1.5 6 5 10 5 10s3.5-4 3.5-6.5A3.5 3.5 0 0 0 5 0zm0 5a1.5 1.5 0 1 1 0-3 1.5 1.5 0 0 1 0 3z"/></svg>Linden St, Eastvale QLD 4000</p>
    <p><svg viewBox="0 0 10 10"><path d="M2 0l2 2.5-1.2 1.3a6 6 0 0 0 3.4 3.4L7.5 6 10 8l-1.5 2C4 10 0 6 0 1.5z"/></svg>+61 (07) 5550 1105</p>
    <p><svg viewBox="0 0 10 10"><path d="M0 2h10v6H0zM0 2l5 3.5L10 2" stroke="#fff" stroke-width=".8"/></svg>riverside@verdantroots.example</p>
  </div>

  <p class="web">WWW.VERDANTROOTS.EXAMPLE</p>
</section>

<section class="page front-cover" aria-label="Front cover">
  <div class="cover-photo" role="img" aria-label="Photograph of fresh green leaves on a soft light background with a stack of smooth pebbles and bamboo stems"></div>
  <div class="brand-disc">
    <p class="brand-name">verdant roots<br>hair salons</p>
  </div>
</section>

<section class="spread" aria-label="Inner price spread">
  <div class="inner left">
    <div class="size-head"><span class="blank"></span><span>S</span><span>M</span><span>L</span><span>XL</span></div>
    <div class="section-band">Cut &amp; Blowdry</div>
    <div class="price-row"><span class="item">Ladies</span><span></span><span>$86</span><span>$99</span><span>$110</span></div>
    <div class="price-row"><span class="item">Fringe</span><span></span><span></span><span></span><span></span></div>
    <div class="price-row"><span class="item sub">Trim</span><span>$15</span><span></span><span></span><span></span></div>
    <div class="price-row"><span class="item sub">Restyle</span><span>$25</span><span></span><span></span><span></span></div>
    <div class="section-band">Blowdry</div>
    <div class="price-row"><span class="item sub">Short to long</span><span>$57</span><span>$67</span><span>$77</span><span>$87</span></div>
    <div class="section-band">Men</div>
    <div class="price-row"><span class="item sub">Cut &amp; style</span><span>$45</span><span></span><span></span><span></span></div>
  </div>

  <div class="inner right">
    <div class="size-head"><span class="blank"></span><span>S</span><span>M</span><span>L</span><span>XL</span></div>
    <div class="section-band">Colour</div>
    <div class="price-row"><span class="item">Regrowth</span><span>$83</span><span>$145</span><span>$165</span><span>$185</span></div>
    <div class="price-row"><span class="item">Full colour tint</span><span>$125</span><span>$189</span><span>$209</span><span>$229</span></div>
    <div class="price-row"><span class="item">Regrowth lightening*</span><span>$165</span><span>$275</span><span>$375</span><span>$475</span></div>
    <div class="price-row"><span class="item">Balayage/ombre*</span><span></span><span></span><span></span><span>$305</span></div>
    <div class="section-band">Pure Bloom</div>
    <div class="price-row"><span class="item">Regrowth</span><span>$99</span><span>$175</span><span>$195</span><span>$205</span></div>
    <div class="price-row"><span class="item">Full colour tint</span><span>$155</span><span></span><span></span><span></span></div>
    <div class="section-band">Foils*</div>
    <div class="price-row"><span class="item">Single*</span><span>$11</span><span>$13</span><span>$17</span><span>$22</span></div>
    <div class="price-row"><span class="item">1/4 Head</span><span>$135</span><span>$155</span><span>$175</span><span>$195</span></div>
    <div class="price-row"><span class="item">1/2 Head</span><span>$185</span><span>$205</span><span>$235</span><span>$265</span></div>
    <div class="price-row"><span class="item">Full Head</span><span>$225</span><span>$265</span><span>$315</span><span>$355</span></div>
    <div class="section-band">Straight</div>
    <div class="price-row"><span class="item">Keratin straightening system</span><span>$365</span><span>$445</span><span>$535</span><span>$565</span></div>
    <p class="note">*Includes colour match &amp; toner<br>*Maximum 6 foils without colour<br>*Minimum charge on a Sunday is $40</p>
    <p class="spread-foot">*Time taken for each service. You will ALWAYS receive a firm price after your consultation.<br>S: to the collarbone | L: to the bra strap | XL: past bra strap</p>
  </div>
</section>

</body>
</html>
```